Website for steady harbor detailing.

Need a homepage, pages for: car and truck detailing, boat detailing, airplane detailing, about us, contact us. I have the domain name through nimbushelm so I will need the design uploaded on my domain. Also hoping to link other domains to this page.I would like to see the logo more pronounced. I would like to see a large phone number link to call my business. The layout looks nice but the pics need to depict car washing and waxing not car mechanics. i would like the colors of the webpage to incorporate the colors found in the logo in some way. I would like links to social media pages
Updates

Target Market(s)

Local customers in Vero Beach, Florida.

Number of Pages Required

5+ page

Colors

Requirements
Must have
• Easy to navigate, attractive pages with pictures and logo, professional looking. must have my phone number and logo very prevalent and links to call or go to home page. I would like links to my social media accounts on the home page.
Nice to have
• Easy to navigate, attractive pages with pictures and logo, professional looking.

```html
<!DOCTYPE html>
<html lang="en">
<head>
<meta charset="utf-8">
<title>Steady Harbor Detailing</title>
<link href="https://fonts.googleapis.com/css2?family=Poppins:wght@400;500;600;700;800&display=swap" rel="stylesheet">
<style>
:root{
  --navy:#28307f;
  --sky:#1aa0e3;
  --red:#e5322d;
  --white:#ffffff;
  --ink:#1d1d1f;
  --footer:#17191d;
  --map:#e8e4da;
}
*{margin:0;padding:0;box-sizing:border-box}
html,body{width:1200px;height:2866px;overflow:hidden;background:var(--white)}
body{position:relative;font-family:"Poppins",sans-serif;color:var(--ink)}
.abs{position:absolute}

/* header */
.header{left:0;top:0;width:1200px;height:141px;background:var(--white)}
.brand{left:48px;top:34px;display:flex;align-items:center;gap:14px}
.brand-dot{width:46px;height:46px;border-radius:50%;background:var(--sky)}
.brand-name{font-weight:700;font-size:27px;line-height:1.05;color:var(--navy)}
.brand-phone{font-weight:700;font-size:15px;color:var(--navy);letter-spacing:2px;margin-top:4px}
.topbar{left:430px;top:0;width:770px;height:71px;background:var(--sky);clip-path:polygon(60px 0,100% 0,100% 100%,0 100%)}
.top-phone{left:580px;top:8px;display:flex;align-items:center;gap:12px;color:var(--white);font-weight:600;font-size:41px}
.socials{left:955px;top:12px;display:flex;gap:8px}
.socials span{width:44px;height:44px;border-radius:50%;background:var(--navy);display:block;border:3px solid var(--white)}
.navbar{left:340px;top:71px;width:860px;height:70px;background:var(--navy);clip-path:polygon(60px 0,100% 0,100% 100%,0 100%)}
.nav-link{top:93px;color:var(--white);font-weight:600;font-size:22px;transform:translateX(-50%)}

/* hero */
.hero{left:0;top:141px;width:1200px;height:791px;background:linear-gradient(120deg,#3c4c6a 0%,#7f8a98 40%,#2c3447 70%,#2a4d85 100%)}
.hero-title{left:397px;transform:translateX(-50%);color:var(--sky);font-weight:700;font-size:64px;line-height:1;white-space:nowrap}
.btn{top:460px;height:54px;display:flex;align-items:center;justify-content:center;color:var(--white);font-weight:600;font-size:20px}
.btn-appt{left:48px;width:328px;background:var(--sky)}
.btn-contact{left:397px;width:325px;background:var(--red)}
.call-label{left:0;width:790px;top:526px;text-align:center;color:var(--white);font-weight:700;font-size:31px}
.call-number{left:0;width:790px;top:561px;text-align:center;color:var(--red);font-weight:800;font-size:82px;letter-spacing:1px}
.tabs{left:200px;top:862px;width:840px;height:70px;background:var(--navy);clip-path:polygon(70px 0,100% 0,calc(100% - 70px) 100%,0 100%)}
.tab-active{left:716px;top:862px;width:316px;height:70px;background:var(--sky);clip-path:polygon(70px 0,100% 0,calc(100% - 70px) 100%,0 100%)}
.tab{top:884px;color:var(--white);font-weight:600;font-size:22px;transform:translateX(-50%)}

/* gallery */
.gallery-title{left:0;width:1200px;top:970px;text-align:center;color:var(--red);font-weight:700;font-size:42px}
.tile{width:283px;height:226px;background:linear-gradient(160deg,#3d6c8e 0%,#4a5360 45%,#9aa1a8 70%,#c46a2a 100%)}
.tile-hover{display:flex;align-items:center;justify-content:center}
.tile-hover::after{content:"";position:absolute;inset:0;background:rgba(196,24,24,.82)}
.view-btn{position:relative;z-index:1;width:48px;height:48px;border-radius:50%;background:var(--white);display:flex;align-items:center;justify-content:center}

/* map */
.map{left:0;top:1699px;width:1200px;height:533px;background:linear-gradient(135deg,#dcd8cc 0%,var(--map) 45%,#e2ddd0 100%)}
.map-label{top:2124px;color:var(--white);font-weight:700;font-size:23px;transform:translateX(-50%);white-space:nowrap;text-shadow:0 0 0 transparent}

/* footer */
.footer{left:0;top:2232px;width:1200px;height:634px;background:linear-gradient(180deg,#2a2d31 0%,var(--footer) 60%,#0d0e10 100%)}
.foot-head{top:2306px;color:var(--white);font-weight:600;font-size:34px}
.foot-item{color:var(--white);font-size:25px;display:flex;align-items:center;gap:18px}
.arrow{width:0;height:0;border-top:12px solid transparent;border-bottom:12px solid transparent;border-left:14px solid var(--white)}
.foot-icon{width:44px;height:44px;border-radius:50%;background:var(--sky)}
.copyright{left:0;width:1200px;top:2776px;text-align:center;color:var(--white);font-weight:600;font-size:23px}
.copyright b{color:var(--sky);font-weight:600}
</style>
</head>
<body>

<header class="abs header"></header>
<div class="abs brand">
  <span class="brand-dot"></span>
  <div>
    <div class="brand-name">Steady Harbor<br>Detailing</div>
    <div class="brand-phone">555-014-2290</div>
  </div>
</div>
<div class="abs topbar"></div>
<div class="abs top-phone">
  <svg width="42" height="42" viewBox="0 0 24 24" aria-hidden="true"><path fill="#fff" d="M6.6 10.8a15.1 15.1 0 0 0 6.6 6.6l2.2-2.2a1 1 0 0 1 1-.25 11.4 11.4 0 0 0 3.6.57 1 1 0 0 1 1 1V20a1 1 0 0 1-1 1A17 17 0 0 1 3 4a1 1 0 0 1 1-1h3.5a1 1 0 0 1 1 1c0 1.25.2 2.45.57 3.6a1 1 0 0 1-.25 1z"/></svg>
  <span>555-014-2290</span>
</div>
<div class="abs socials"><span></span><span></span><span></span><span></span></div>
<nav class="abs navbar"></nav>
<a class="abs nav-link" style="left:550px">HOME</a>
<a class="abs nav-link" style="left:718px">ABOUT US</a>
<a class="abs nav-link" style="left:908px">SERVICES&#8964;</a>
<a class="abs nav-link" style="left:1083px">CONTACT</a>

<section class="abs hero" role="img" aria-label="Photo of a worker washing a soapy car in a detailing bay"></section>
<h1 class="abs hero-title" style="top:285px">CAR</h1>
<div class="abs hero-title" style="top:370px">WASH &amp; WAX</div>
<a class="abs btn btn-appt">GET AN APPOINTMENT</a>
<a class="abs btn btn-contact">CONTACT US</a>
<div class="abs call-label">OR CALL US NOW!</div>
<a class="abs call-number">555-014-2290</a>
<div class="abs tabs"></div>
<div class="abs tab-active"></div>
<span class="abs tab" style="left:325px">AIRPLANE</span>
<span class="abs tab" style="left:512px">BOAT</span>
<span class="abs tab" style="left:697px">TRUCK</span>
<span class="abs tab" style="left:866px">CAR</span>

<h2 class="abs gallery-title">CAR GALLERY</h2>
<div class="abs tile" style="left:88px;top:1066px" role="img" aria-label="Car detailing gallery photo"></div>
<div class="abs tile" style="left:459px;top:1066px" role="img" aria-label="Car detailing gallery photo"></div>
<div class="abs tile" style="left:835px;top:1066px" role="img" aria-label="Car detailing gallery photo"></div>
<div class="abs tile" style="left:88px;top:1397px" role="img" aria-label="Car detailing gallery photo"></div>
<div class="abs tile tile-hover" style="left:459px;top:1397px" role="img" aria-label="Car detailing gallery photo with view overlay">
  <span class="view-btn"><svg width="26" height="26" viewBox="0 0 24 24" aria-hidden="true"><path fill="#c41818" d="M12 5C6.5 5 2.7 9.3 1.5 12c1.2 2.7 5 7 10.5 7s9.3-4.3 10.5-7C21.3 9.3 17.5 5 12 5zm0 11a4 4 0 1 1 0-8 4 4 0 0 1 0 8zm0-6a2 2 0 1 0 0 4 2 2 0 0 0 0-4z"/></svg></span>
</div>
<div class="abs tile" style="left:835px;top:1397px" role="img" aria-label="Car detailing gallery photo"></div>

<section class="abs map" role="img" aria-label="Street map of the service area"></section>
<span class="abs map-label" style="left:178px">CAR WASH</span>
<span class="abs map-label" style="left:459px">BOAT WASH</span>
<span class="abs map-label" style="left:740px">AIRPLANE WASH</span>
<span class="abs map-label" style="left:1022px">TRUCK WASH</span>

<footer class="abs footer" role="img" aria-label="Dark photo of a wet pickup truck behind the footer"></footer>
<h3 class="abs foot-head" style="left:118px">OUR SERVICES</h3>
<h3 class="abs foot-head" style="left:460px">CONTACT US</h3>
<h3 class="abs foot-head" style="left:841px">LIKE US ON</h3>

<div class="abs foot-item" style="left:118px;top:2404px"><span class="arrow"></span>Car Detailing</div>
<div class="abs foot-item" style="left:118px;top:2475px"><span class="arrow"></span>Truck Detailing</div>
<div class="abs foot-item" style="left:118px;top:2546px"><span class="arrow"></span>Boat Detailing</div>
<div class="abs foot-item" style="left:118px;top:2616px"><span class="arrow"></span>Airplane Detailing</div>

<div class="abs foot-item" style="left:458px;top:2404px">555-014-2290</div>
<div class="abs foot-item" style="left:458px;top:2475px">hello@steadyharbor.example</div>
<div class="abs foot-item" style="left:458px;top:2546px">1234 Sample Address, Here</div>

<div class="abs foot-item" style="left:837px;top:2400px"><span class="foot-icon"></span>friendwall.com</div>
<div class="abs foot-item" style="left:837px;top:2471px"><span class="foot-icon"></span>chatterline.com</div>
<div class="abs foot-item" style="left:837px;top:2542px"><span class="foot-icon"></span>pinboardly.com</div>
<div class="abs foot-item" style="left:837px;top:2612px"><span class="foot-icon"></span>snapgrid.com</div>

<p class="abs copyright">© Copyrights 2018 <b>Company</b> | All Rights Reserved.</p>

</body>
</html>
```